Professional Photography Business cards

I need business cards that include my logo which I have uploaded. I run a photography business. I am open to ideas but I would like one side to have my logo and the other side to have my contact info. I don't have a website made but I do own a website domain. I have uploaded 2 different logo color schemes. My business colors are Blue, black , and white.

Business Name
Business Phone Number
Business Email
Business Website address
Instagram

Industry/Entity Type

Professional Photography

Contact Information for Business Card

Phone Number: 916-384-7702 email: info@tlane-studio.example Instagram: @t.lanestudio website doman- www.tlane-studio.example

Requirements
Must have
• I like the idea of a business card with a full black background front and back of card. My colors must include royal blue, black, and white

```html
<!DOCTYPE html>
<html lang="en">
<head>
<meta charset="utf-8">
<title>T. Lane Studio – Business Card</title>
<link href="https://fonts.googleapis.com/css2?family=Poppins:wght@300;400;500&display=swap" rel="stylesheet">
<style>
  :root {
    --page-bg: #e4e0e0;
    --card-black: #000000;
    --panel-light: #f1ecec;
    --panel-shade: #e6dfe0;
    --royal-blue: #1c1aa6;
    --ink: #111111;
  }
  html, body {
    margin: 0;
    width: 1200px;
    height: 900px;
    overflow: hidden;
    background: var(--page-bg);
  }
  .canvas {
    position: relative;
    width: 1200px;
    height: 900px;
  }
  .business-card {
    position: absolute;
    left: 100px;
    top: 141px;
    width: 1000px;
    height: 618px;
    box-shadow: 0 18px 40px rgba(0,0,0,0.18);
  }
  .business-card svg { display: block; width: 100%; height: 100%; }
  .contact-text {
    font-family: "Poppins", sans-serif;
    font-weight: 400;
    font-size: 29px;
    fill: var(--ink);
  }
  .brand-name {
    font-family: "Poppins", sans-serif;
    font-weight: 500;
    font-size: 54px;
    fill: var(--royal-blue);
  }
  .icon-stroke { fill: none; stroke: var(--royal-blue); stroke-width: 2.6; stroke-linecap: round; stroke-linejoin: round; }
  .icon-fill { fill: var(--royal-blue); }
</style>
</head>
<body>
<main class="canvas">
  <section class="business-card" aria-label="T. Lane Studio contact card">
    <svg viewBox="0 0 1090 673" xmlns="http://www.w3.org/2000/svg">
      <defs>
        <linearGradient id="panelTone" x1="0" y1="0" x2="1" y2="1">
          <stop offset="0" stop-color="var(--panel-light)"/>
          <stop offset="1" stop-color="var(--panel-shade)"/>
        </linearGradient>
      </defs>

      <rect class="card-base" x="0" y="0" width="1090" height="673" fill="var(--card-black)"/>

      <path class="camera-panel" fill="url(#panelTone)"
        d="M0 152 H388 L428 58 Q440 30 470 30 H742 Q772 30 786 58 L822 152 H1000
           Q1065 152 1065 215 V595 Q1065 655 1000 655 H0 Z"/>

      <rect class="viewfinder-slot" x="475" y="58" width="270" height="24" rx="12" fill="var(--card-black)"/>

      <rect class="flash-window" x="898" y="185" width="102" height="56" rx="16" fill="var(--card-black)"/>
      <rect x="912" y="197" width="42" height="20" fill="var(--panel-light)"/>

      <g class="brand-lockup">
        <text class="brand-name" x="385" y="318">T. Lane Studio</text>
        <circle cx="830" cy="300" r="26" fill="none" stroke="var(--ink)" stroke-width="4"/>
      </g>

      <g class="contact-list">
        <rect class="icon-stroke" x="37" y="405" width="28" height="28" rx="6"/>
        <text class="contact-text" x="77" y="430">@t.lanestudio</text>

        <path class="icon-fill" d="M41 498 q3 -3 6 0 l5 6 q2 3 -1 5 l-3 2 q3 7 10 11 l2 -3 q2 -3 5 -1 l6 5 q3 3 0 6 l-3 3 q-6 5 -18 -4 q-12 -10 -14 -21 q-1 -6 5 -9z"/>
        <text class="contact-text" x="77" y="518">916-384-7702</text>

        <rect class="icon-fill" x="36" y="541" width="30" height="20"/>
        <path d="M36 541 L51 553 L66 541" fill="none" stroke="var(--panel-light)" stroke-width="2.4"/>
        <text class="contact-text" x="77" y="558">info@tlane-studio.example</text>

        <circle class="icon-stroke" cx="51" cy="588" r="13"/>
        <ellipse class="icon-stroke" cx="51" cy="588" rx="6" ry="13"/>
        <line class="icon-stroke" x1="38" y1="588" x2="64" y2="588"/>
        <line class="icon-stroke" x1="40" y1="581" x2="62" y2="581"/>
        <line class="icon-stroke" x1="40" y1="595" x2="62" y2="595"/>
        <text class="contact-text" x="77" y="598">www.tlane-studio.example</text>
      </g>
    </svg>
  </section>
</main>
</body>
</html>
```